business card deign

Logo needs the following on it.
1. attached logo
2. Tagline - "From chilled cans to loud speakers...we bring the good times!"
3. Name- Dalton Pikes, Founder and CPO
4. Address - 412 E. Carver Avenue, Ste 2207, Tampa, FL. 33917
5. Phone - 555.318.4726

```html
<!DOCTYPE html>
<html lang="en">
<head>
<meta charset="utf-8">
<title>Hopvale Business Card</title>
<link rel="stylesheet" href="https://fonts.googleapis.com/css2?family=Roboto:wght@300;400;500;700&display=swap">
<style>
  :root {
    --bg: #1b1b1c;
    --card: #2b2b2c;
    --ink: #f2f2f2;
    --ink-soft: #c9c9c9;
    --gloss: #0e0e0e;
    --rule: #8a8a8a;
  }
  * { margin: 0; padding: 0; box-sizing: border-box; }
  html, body {
    width: 1200px; height: 825px; overflow: hidden;
    background: var(--bg);
    font-family: "Roboto", Arial, sans-serif;
  }
  .sheet {
    width: 1200px; height: 825px;
    display: flex; align-items: center; justify-content: center; gap: 40px;
  }
  .card {
    position: relative;
    width: 560px; height: 320px;
    background: var(--card);
    border-radius: 3px;
  }

  /* Back side: large brand name */
  .card-back {
    display: flex; align-items: center; justify-content: center;
  }
  .card-back .brand-large {
    display: flex; align-items: center; gap: 18px;
    font-weight: 700; font-size: 54px; letter-spacing: 14px;
    color: var(--gloss);
  }
  .card-back .brand-mark {
    width: 46px; height: 46px; border-radius: 50%;
    background: var(--gloss);
  }

  /* Front side: brand, contact details, tagline */
  .card-front .brand {
    position: absolute; left: 40px; top: 96px; width: 200px;
    display: flex; flex-direction: column; align-items: center; gap: 16px;
  }
  .card-front .brand-mark {
    width: 70px; height: 70px; border-radius: 50%;
    background: var(--ink);
  }
  .card-front .brand-name {
    font-weight: 500; font-size: 28px; letter-spacing: 9px;
    color: var(--ink);
  }
  .card-front .divider {
    position: absolute; left: 262px; top: 56px;
    width: 1px; height: 170px; background: var(--rule);
  }
  .contact {
    position: absolute; left: 286px; top: 62px;
    color: var(--ink-soft); font-size: 13.5px; line-height: 1.35;
  }
  .contact .person {
    font-weight: 700; font-size: 19px; color: var(--ink);
    letter-spacing: 0.3px;
  }
  .contact .role { margin-bottom: 12px; }
  .contact .address { margin-bottom: 12px; }
  .contact .line { display: flex; align-items: center; gap: 8px; }
  .contact .line svg { width: 12px; height: 12px; flex: none; }
  .contact .icon-phone { fill: var(--ink-soft); }
  .contact .icon-mail { fill: none; stroke: var(--ink-soft); stroke-width: 2; }
  .tagline {
    position: absolute; left: 0; right: 0; bottom: 32px;
    text-align: center; font-size: 13px; font-weight: 300;
    color: var(--ink-soft); letter-spacing: 0.4px;
  }
</style>
</head>
<body>
  <main class="sheet">
    <section class="card card-back" aria-label="Card back">
      <div class="brand-large">
        <span class="brand-mark"></span>
        <span>HOPVALE</span>
      </div>
    </section>

    <section class="card card-front" aria-label="Card front">
      <div class="brand">
        <span class="brand-mark"></span>
        <span class="brand-name">HOPVALE</span>
      </div>
      <div class="divider"></div>
      <div class="contact">
        <p class="person">DALTON PIKES</p>
        <p class="role">Founder and CPO</p>
        <p class="address">412 E. Carver Avenue,<br>Ste 2207, Tampa, FL. 33917</p>
        <p class="line">
          <svg class="icon-phone" viewBox="0 0 24 24" aria-hidden="true"><path d="M6.6 10.8a15.1 15.1 0 0 0 6.6 6.6l2.2-2.2a1 1 0 0 1 1-.25 11.4 11.4 0 0 0 3.6.57 1 1 0 0 1 1 1V20a1 1 0 0 1-1 1A17 17 0 0 1 3 4a1 1 0 0 1 1-1h3.5a1 1 0 0 1 1 1c0 1.25.2 2.45.57 3.6a1 1 0 0 1-.25 1z"/></svg>
          555.318.4726
        </p>
        <p class="line">
          <svg class="icon-mail" viewBox="0 0 24 24" aria-hidden="true"><rect x="2" y="5" width="20" height="14" rx="1"/><path d="M3 6l9 7 9-7"/></svg>
          info@hopvalegear.com
        </p>
      </div>
      <p class="tagline">From chilled cans to loud speakers...we bring the good times!</p>
    </section>
  </main>
</body>
</html>
```